Business Card Design for company

We want new business cards. We'd like something different-- yet still highly professional. Our tagline is Providing leadership, delivering success. Stock photos are ok, as long as they are relevant and look upscale.

Target Market(s)

Architecture/Business Management Consulting/Engineering Consulting

Contact Information for Business Card

dark gray background with pops of blue might be good, but you tell me. You're the designers. Rounded corners might be nice, but again, you tell me.

Font styles to use
Serif
Sans Serif

Colors
3276b5
5c5c5c
9d9d9d
fbfbfb

Requirements
Nice to have
• Something different, but still very professional.

```html
<!DOCTYPE html>
<html lang="en">
<head>
<meta charset="utf-8">
<title>Trevane International – Business Card</title>
<link href="https://fonts.googleapis.com/css2?family=Work+Sans:wght@400;500;600&display=swap" rel="stylesheet">
<style>
  :root {
    --stage: #161616;
    --card-back: #2c2c2d;
    --card-front: #2a2a2b;
    --blue: #3276b5;
    --mid-gray: #5c5c5c;
    --light-gray: #9d9d9d;
    --white: #fbfbfb;
  }
  * { box-sizing: border-box; margin: 0; padding: 0; }
  html, body {
    width: 1200px; height: 900px; overflow: hidden;
    background: var(--stage);
    font-family: "Work Sans", Arial, sans-serif;
  }
  .stage {
    width: 1200px; height: 900px;
    display: flex; flex-direction: column; align-items: center; justify-content: center;
    gap: 40px;
  }
  .card {
    width: 700px; height: 400px; border-radius: 6px; position: relative; overflow: hidden;
    box-shadow: 0 14px 30px rgba(0,0,0,.55);
  }
  /* Back side */
  .card--back { background: var(--card-back); }
  .card--back .world-map {
    position: absolute; left: 60px; top: 30px; width: 580px; height: 340px;
    border-radius: 40%;
    background: radial-gradient(ellipse at center, rgba(157,157,157,.22) 0%, rgba(157,157,157,.08) 55%, rgba(157,157,157,0) 75%);
  }
  .card--back .brand-name {
    position: absolute; inset: 0; display: flex; align-items: center; justify-content: center;
    color: var(--blue); font-weight: 500; font-size: 46px; letter-spacing: 1px;
  }
  /* Front side */
  .card--front { background: var(--card-front); color: var(--white); }
  .claim {
    position: absolute; top: 26px; left: 0; right: 0; text-align: center;
    color: var(--light-gray); font-size: 15px; letter-spacing: .5px;
  }
  .brand-block {
    position: absolute; left: 48px; top: 128px; width: 300px;
    color: var(--blue); font-weight: 600; line-height: 1;
  }
  .brand-block .word-main { display: block; font-size: 62px; letter-spacing: 1px; }
  .brand-block .word-sub { display: block; font-size: 28px; letter-spacing: 4px; margin-top: 8px; }
  .divider {
    position: absolute; left: 378px; top: 112px; width: 2px; height: 176px; background: var(--white);
  }
  .contact { position: absolute; left: 410px; top: 112px; font-size: 16px; line-height: 1.35; }
  .contact .person { color: var(--blue); font-size: 26px; font-weight: 500; letter-spacing: 2px; text-transform: uppercase; }
  .contact .role { font-size: 16px; margin-bottom: 12px; }
  .contact address { font-style: normal; margin-bottom: 8px; }
  .contact ul { list-style: none; }
  .contact li { display: flex; align-items: center; gap: 8px; }
  .contact svg { width: 12px; height: 12px; flex: none; }
  .slogan {
    position: absolute; bottom: 30px; left: 0; right: 0; text-align: center;
    font-size: 19px; font-weight: 500; letter-spacing: .5px;
  }
</style>
</head>
<body>
<main class="stage">
  <section class="card card--back">
    <div class="world-map" role="img" aria-label="Dotted world map background"></div>
    <div class="brand-name">Trevane</div>
  </section>

  <section class="card card--front">
    <p class="claim">Trusted Construction Management Advisor since 1999.</p>
    <div class="brand-block">
      <span class="word-main">Trevane</span>
      <span class="word-sub">International</span>
    </div>
    <div class="divider"></div>
    <div class="contact">
      <p class="person">Daniel Harrow</p>
      <p class="role">Director</p>
      <address>214b Calder Street,<br>Westbrook, NZ, 8042</address>
      <ul>
        <li><svg viewBox="0 0 12 12"><path d="M2.5 1h2l1 3-1.5 1a6 6 0 0 0 3 3l1-1.5 3 1v2A1 1 0 0 1 10 11 9 9 0 0 1 1 2a1 1 0 0 1 1.5-1z" fill="var(--blue)"/></svg>(555) 014-2290</li>
        <li><svg viewBox="0 0 12 12"><rect x="1" y="2.5" width="10" height="7" rx="1" fill="none" stroke="var(--blue)"/><path d="M1 3l5 3.5L11 3" fill="none" stroke="var(--blue)"/></svg>info@trevaneintl.com</li>
        <li><svg viewBox="0 0 12 12"><circle cx="6" cy="6" r="5" fill="none" stroke="var(--blue)"/><path d="M1 6h10M6 1c-2.5 3-2.5 7 0 10M6 1c2.5 3 2.5 7 0 10" fill="none" stroke="var(--blue)"/></svg>www.trevaneintl.com</li>
      </ul>
    </div>
    <p class="slogan">Providing Leadership, Delivering Success</p>
  </section>
</main>
</body>
</html>
```